Bramble Hounds Dog Behaviour, Training and Natural Healthcare Website

Hey there,
I need a webpage designed for my new business. It needs to be something authentic, new, fresh and representative of my business ethos. I operate out of Newcastle, NSW. I believe my job is to keep dogs alive and in their home by promoting communication and connection between dogs and their owners. This can't be achieved through training and behaviour alone. Nutritional guidance and environmental adaptation are often needed to complete the package and increase the success rate for these programs. I provide practical services such as walking coaching, nutrition profiling, behavioural modification, puppy minding, board and train programs for puppies and young dogs, training, basic and complex skills training, physical therapies and natural healthcare options. In effect taking care of the whole dog.
My motto is = Happy dogs, happy owners.
My catch cry is = promoting communication and connection between dogs and their owners.

I have in mind pages that can also link to other pages when an icon is clicked. I need a homepage, sections to explain what each of my services do (4 - which could be independent pages so I can attach photos) and a gallery. I want to have multi page function, an online capability for future retail, ability to amend and update content myself, an online booking and payment facility. My interests lie in I have seen many successes via and environmental modifications.
I've attached the logo which features prominently on my business card and Facebook page. The corporate colours are Blue with a splash of red and white. The dog being held in the healing hands must feature.

Thanks!

Target Market(s)

Australian Pet Dog Owners

Industry/Entity Type

Communication

Coding

Colors
0355a3
ec1f27
ffffff

Requirements
Must have
• The business colours (blue with a splash of red and white), the dog in the healing hands
Should not have
• Pawprints or cartoon animals

```html
<!DOCTYPE html>
<html lang="en">
<head>
<meta charset="utf-8">
<title>Bramble Hounds – Happy Dogs, Happy Owners</title>
<link href="https://fonts.googleapis.com/css2?family=Arimo:wght@400;700&family=Lato:wght@400;700&family=Open+Sans:wght@400;600&display=swap" rel="stylesheet">
<style>
:root{
  --blue:#0355a3;
  --blue-light:#1e84d8;
  --blue-dark:#0a4a93;
  --red:#ec1f27;
  --white:#ffffff;
  --page:#fdf8f3;
  --ink:#333333;
  --muted:#555555;
  --rule:#d9d4cf;
}
*{margin:0;padding:0;box-sizing:border-box}
html,body{width:709px;height:1200px;overflow:hidden}
body{position:relative;background:var(--page);font-family:"Arimo",Arial,sans-serif;color:var(--ink)}
.abs{position:absolute}

/* header */
.site-header{left:0;top:0;width:709px;height:85px;background:linear-gradient(#0a7fd6,#0660b8 70%,#0355a3)}
.brand-mark{left:60px;top:4px;width:52px;height:52px;border-radius:50%;background:var(--white);border:3px solid var(--red)}
.brand-name{left:20px;top:56px;width:136px;text-align:center;color:var(--white);font-family:"Lato",sans-serif;font-weight:700;font-size:12px;letter-spacing:.3px}
.brand-tag{left:20px;top:73px;width:136px;text-align:center;color:var(--white);font-size:7px}
.social-top{top:28px;width:9px;height:9px;border-radius:50%;background:var(--white)}
.contact-btn{left:598px;top:25px;width:74px;height:18px;background:var(--white);color:#222;font-size:7.5px;text-align:center;line-height:18px;letter-spacing:.3px}
.main-nav{top:62px;color:var(--white);font-size:7.5px;letter-spacing:.2px}
.main-nav.is-active{left:366px;top:60px;width:45px;height:15px;border:1px solid var(--white);border-radius:2px;text-align:center;line-height:13px}

/* hero */
.hero-photo{left:0;top:85px;width:709px;height:318px;
  background:
    radial-gradient(ellipse 180px 200px at 190px 170px,rgba(60,70,110,.55),rgba(60,70,110,0) 70%),
    radial-gradient(ellipse 120px 110px at 250px 270px,rgba(20,20,20,.6),rgba(20,20,20,0) 75%),
    radial-gradient(ellipse 260px 90px at 560px 60px,rgba(150,170,70,.55),rgba(150,170,70,0) 75%),
    linear-gradient(180deg,#2f4620 0%,#4d6a2a 22%,#7d8a3e 42%,#8f8a64 60%,#a8a08a 80%,#b4ac98 100%)}
.hero-panel{left:354px;top:202px;width:320px;height:146px;background:rgba(30,26,20,.82);color:var(--white);text-align:right;padding:12px 17px}
.hero-title{font-family:"Lato",sans-serif;font-size:24px;letter-spacing:.5px}
.hero-sub{font-family:"Lato",sans-serif;font-size:12px;margin-top:6px}
.hero-copy{font-family:"Lato",sans-serif;font-size:8px;line-height:11.5px;margin-top:9px;font-weight:700}
.slide-btn{top:358px;width:18px;height:18px;border-radius:50%}

/* about */
.section-title{font-size:15.5px;font-weight:400;color:#222}
.body-copy{font-size:7px;line-height:11px;color:var(--muted)}
.about-photo{left:38px;top:500px;width:150px;height:100px;
  background:
    radial-gradient(ellipse 60px 26px at 75px 52px,#f1e2c4,rgba(241,226,196,0) 100%),
    radial-gradient(circle 22px at 22px 52px,#8a5a34,rgba(138,90,52,0) 100%),
    radial-gradient(circle 22px at 128px 52px,#8a5a34,rgba(138,90,52,0) 100%),
    radial-gradient(ellipse at 50% 40%,#fafafa,#dcdcdc)}
.btn-red{background:var(--red);color:var(--white);font-size:9px;text-align:center}

/* services */
.service-row{left:478px;width:194px;height:24px;border-bottom:1px solid var(--rule);font-size:8.5px;color:#333;line-height:18px}
.toggle{right:0;top:0;width:18px;height:18px;background:#d8d8d8}
.toggle svg{position:absolute;left:5px;top:5px}

.divider{left:38px;top:714px;width:636px;height:1px;background:var(--rule)}

/* news */
.news-band{left:34px;top:746px;width:640px;height:69px;background:var(--white)}
.news-label{left:34px;top:746px;width:152px;height:69px;background:linear-gradient(var(--blue-light),var(--blue));color:var(--white);font-size:15.5px;line-height:69px;padding-left:29px}
.news-photo{left:209px;top:758px;width:61px;height:46px;
  background:
    radial-gradient(ellipse 26px 14px at 32px 18px,#7a4420,#a8683a 60%,rgba(168,104,58,0) 100%),
    radial-gradient(ellipse 30px 20px at 32px 28px,#f4f1ec,rgba(244,241,236,0) 100%),
    linear-gradient(135deg,#d8d2c8,#f0ede8)}

/* testimonials */
.quote-card{top:894px;width:186px;height:62px;background:var(--white);box-shadow:0 0 4px rgba(0,0,0,.08);font-family:"Open Sans",sans-serif;font-size:7.2px;line-height:12px;color:#444;padding:10px 30px 10px 10px}
.quote-tail{position:absolute;left:16px;bottom:-7px}
.col-rule{top:894px;width:1px;height:98px;background:#e2ddd8}
.avatar{top:973px;width:34px;height:34px;border-radius:50%}
.client-name{top:986px;font-family:"Open Sans",sans-serif;font-size:7px;color:#444}
.dot{top:1030px;width:8px;height:8px;border-radius:50%;border:1.3px solid var(--red)}

/* footer */
.site-footer{left:0;top:1089px;width:709px;height:111px;background:linear-gradient(var(--blue-light),var(--blue) 60%,var(--blue-dark))}
.foot-nav{top:1114px;color:var(--white);font-size:7.5px;font-weight:700}
.foot-nav.is-active{left:36px;top:1110px;width:36px;height:18px;border:1px solid var(--white);border-radius:9px;text-align:center;line-height:16px}
.foot-social{top:1112px;width:9px;height:9px;border-radius:50%;background:var(--white)}
.foot-icon{top:1162px;width:15px;height:15px;border-radius:50%;background:var(--white)}
.foot-icon svg{position:absolute;left:3px;top:3px}
.foot-text{color:var(--white);font-size:6px;font-weight:700;line-height:8px}
</style>
</head>
<body>

<header class="abs site-header"></header>
<div class="abs brand-mark"></div>
<div class="abs brand-name">BRAMBLE HOUNDS</div>
<div class="abs brand-tag">HAPPY DOGS, HAPPY OWNERS</div>
<span class="abs social-top" style="left:518px"></span>
<span class="abs social-top" style="left:535px"></span>
<span class="abs social-top" style="left:553px"></span>
<span class="abs social-top" style="left:571px"></span>
<div class="abs contact-btn">CONTACT</div>
<nav>
  <span class="abs main-nav is-active">HOME</span>
  <span class="abs main-nav" style="left:419px">ABOUT US</span>
  <span class="abs main-nav" style="left:475px">SERVICE</span>
  <span class="abs main-nav" style="left:522px">PRODUCTS</span>
  <span class="abs main-nav" style="left:580px">BLOG</span>
  <span class="abs main-nav" style="left:619px">TESTIMONIALS</span>
</nav>

<section>
  <div class="abs hero-photo" role="img" aria-label="Trainer in a forest clearing signalling to a black labrador sitting on a path"></div>
  <div class="abs hero-panel">
    <div class="hero-title">BRAMBLE HOUNDS</div>
    <div class="hero-sub">We are Dog behaviour study and training company</div>
    <p class="hero-copy">Vestibulum pretium, nisi vel convallis convallis, mi turpis feugiat leo, posuere feugiat nisl risus at erat. Cum sociis natoque penatibus et magnis dis parturient montes, nascetur ridiculus mus. Aliquam at cursus nisl. Duis nec odio mi. Donec lacinia lectus at bibendum volutpat. Donec vestibulum sem quis consectetur aliquet.</p>
  </div>
  <div class="abs slide-btn" style="left:634px;background:var(--white)">
    <svg width="18" height="18"><path d="M10 5 L6 9 L10 13" stroke="#888" stroke-width="1.6" fill="none"/></svg>
  </div>
  <div class="abs slide-btn" style="left:657px;background:var(--blue)">
    <svg width="18" height="18"><path d="M8 5 L12 9 L8 13" stroke="#fff" stroke-width="1.6" fill="none"/></svg>
  </div>
</section>

<section>
  <h2 class="abs section-title" style="left:38px;top:430px">About Us</h2>
  <p class="abs body-copy" style="left:36px;top:460px;width:416px">Vestibulum pretium, nisi vel convallis convallis, mi turpis feugiat leo, posuere feugiat nisl risus at erat. Cum sociis natoque penatibus et magnis dis parturient montes, nascetur ridiculus mus. Aliquam at cursus nisl. Duis nec odio mi. Donec lacinia lectus at bibendum volutpat. Donec vestibulum sem quis consectetur aliquet. Proin at nibh vitae diam sollicitudin bibendum.</p>
  <div class="abs about-photo" role="img" aria-label="Dog chew bone on a pale grey background"></div>
  <p class="abs body-copy" style="left:197px;top:500px;width:248px;text-align:justify">Lorem ipsum dolor sit amet, consectetur adipiscing elit. Ut volutpat lacus eu dictum sagittis. Ut dictum vulputate augue nec euismod. Curabitur cursus magna ut turpis gravida sagittis. Nam ultrices tristique risus, condimentum dignissim lectus euismod a. Curabitur varius lacinia ex, sed volutpat nunc faucibus vel. Nullam justo mauris, ullamcorper nec rhoncus nec, scelerisque et lorem. Sed ut augue non risus efficitur pellentesque. Nam pulvinar nunc sapien,</p>
  <p class="abs body-copy" style="left:38px;top:612px;width:408px;text-align:justify">Lorem ipsum dolor sit amet, consectetur adipiscing elit. Ut volutpat lacus eu dictum sagittis. Ut dictum vulputate augue nec euismod. Curabitur cursus magna ut turpis gravida sagittis. Nam ultrices tristique risus, condimentum dignissim lectus euismod a. Curabitur varius lacinia ex, sed volutpat nunc faucibus vel.</p>
  <div class="abs btn-red" style="left:350px;top:670px;width:96px;height:20px;line-height:20px">Read More</div>
</section>

<section>
  <h2 class="abs section-title" style="left:477px;top:430px">Our Services</h2>
  <p class="abs body-copy" style="left:478px;top:454px">We wont let you down, we are here to make you feel..</p>
  <div class="abs service-row" style="top:482px">Walking coaching
    <span class="abs toggle"><svg width="8" height="8"><path d="M1 4H7" stroke="#333" stroke-width="1.4"/></svg></span>
  </div>
  <p class="abs body-copy" style="left:478px;top:507px;width:194px;line-height:10.3px">Our management consulting services address our clients' crucial issues and opportunities: strategy, organizational structure, business development, operations, marketing and transformation.</p>
  <div class="abs btn-red" style="left:478px;top:561px;width:57px;height:18px;line-height:18px;font-size:8px">Read More</div>
  <div class="abs service-row" style="top:598px">Nutrition profiling
    <span class="abs toggle"><svg width="8" height="8"><path d="M1 4H7M4 1V7" stroke="#333" stroke-width="1.4"/></svg></span>
  </div>
  <div class="abs service-row" style="top:621px">Behavioural modification
    <span class="abs toggle" style="top:3px"><svg width="8" height="8"><path d="M1 4H7M4 1V7" stroke="#333" stroke-width="1.4"/></svg></span>
  </div>
  <div class="abs service-row" style="top:645px">Puppy minding
    <span class="abs toggle" style="top:3px"><svg width="8" height="8"><path d="M1 4H7M4 1V7" stroke="#333" stroke-width="1.4"/></svg></span>
  </div>
  <div class="abs service-row" style="top:668px">Training
    <span class="abs toggle" style="top:5px"><svg width="8" height="8"><path d="M1 4H7M4 1V7" stroke="#333" stroke-width="1.4"/></svg></span>
  </div>
</section>

<div class="abs divider"></div>

<section>
  <div class="abs news-band"></div>
  <div class="abs news-label">Latest News</div>
  <svg class="abs" style="left:186px;top:771px" width="15" height="20"><path d="M0 0L15 10L0 20Z" fill="#0a6cc4"/></svg>
  <div class="abs news-photo" role="img" aria-label="Bowl of dry dog food"></div>
  <h3 class="abs" style="left:292px;top:754px;font-size:12.5px;font-weight:400;color:#333">Lorem ipsum dolor</h3>
  <p class="abs body-copy" style="left:292px;top:775px;width:366px;line-height:10.5px">Vestibulum pretium, nisi vel convallis convallis, mi turpis feugiat leo, posuere feugiat nisl risus at erat. Cum sociis natoque penatibus et magnis dis parturient montes, nascetur ridiculus mus. Aliquam at cursus nisl.</p>
  <span class="abs" style="left:601px;top:799px;font-size:7px;color:var(--red)">Read More &gt;&gt;</span>
</section>

<section>
  <h2 class="abs section-title" style="left:38px;top:856px">Client Testimonials</h2>
  <svg class="abs" style="left:646px;top:859px" width="28" height="12"><path d="M10 0L0 6L10 12Z" fill="#c8d4e0"/><path d="M18 0L28 6L18 12Z" fill="var(--blue)"/></svg>

  <div class="abs quote-card" style="left:39px">From someone who never trained with music out on the road due to safety concerns I'm in love with the SoundMates. Great
    <svg class="quote-tail" width="12" height="8"><path d="M0 0H12L2 8Z" fill="#fff"/></svg></div>
  <div class="abs quote-card" style="left:262px">Because I like my music loud, there is always a danger that I cannot hear traffic or other noises when training. The SoundMates allows
    <svg class="quote-tail" width="12" height="8"><path d="M0 0H12L2 8Z" fill="#fff"/></svg></div>
  <div class="abs quote-card" style="left:487px">It's a completely different experience form riding with conventional headphones... The awareness, and where cars where coming
    <svg class="quote-tail" width="12" height="8"><path d="M0 0H12L2 8Z" fill="#fff"/></svg></div>

  <div class="abs col-rule" style="left:242px"></div>
  <div class="abs col-rule" style="left:466px"></div>

  <div class="abs avatar" style="left:38px;background:radial-gradient(circle at 50% 55%,#e8c8ac,#b88c6a 70%,#7a5a42)" role="img" aria-label="Client portrait"></div>
  <span class="abs client-name" style="left:78px">Lena Marwick</span>
  <div class="abs avatar" style="left:261px;background:radial-gradient(circle at 50% 55%,#d8b094,#5a3a2c 65%,#1e1612)" role="img" aria-label="Client portrait"></div>
  <span class="abs client-name" style="left:301px">Tess Harlow</span>
  <div class="abs avatar" style="left:486px;background:radial-gradient(circle at 50% 55%,#e4c6b0,#a88a78 60%,#3a3a3a)" role="img" aria-label="Client portrait"></div>
  <span class="abs client-name" style="left:526px">Owen Fairley</span>

  <span class="abs dot" style="left:334px;background:var(--red)"></span>
  <span class="abs dot" style="left:344px"></span>
  <span class="abs dot" style="left:354px"></span>
</section>

<footer>
  <div class="abs site-footer"></div>
  <span class="abs foot-nav is-active">HOME</span>
  <span class="abs foot-nav" style="left:82px">ABOUT US</span>
  <span class="abs foot-nav" style="left:138px">SERVICE</span>
  <span class="abs foot-nav" style="left:185px">PRODUCTS</span>
  <span class="abs foot-nav" style="left:243px">BLOG</span>
  <span class="abs foot-nav" style="left:282px">TESTIMONIALS</span>

  <span class="abs foot-social" style="left:612px"></span>
  <span class="abs foot-social" style="left:630px"></span>
  <span class="abs foot-social" style="left:648px"></span>
  <span class="abs foot-social" style="left:667px"></span>

  <span class="abs foot-icon" style="left:36px"><svg width="9" height="9"><path d="M4.5 1L1 4.5H2.3V8H6.7V4.5H8Z" fill="var(--blue)"/></svg></span>
  <p class="abs foot-text" style="left:55px;top:1163px">14 WATTLE LANE, HILLCREST BAY, NORTHSHORE<br>2391, AUSTRALIA</p>
  <span class="abs foot-icon" style="left:250px"><svg width="9" height="9"><path d="M2 1L3.5 1L4.2 3L3.2 3.8Q4 5.6 5.6 6.2L6.4 5.2L8 6V7.6Q4.5 8 1.5 4Q1 2 2 1Z" fill="var(--blue)"/></svg></span>
  <p class="abs foot-text" style="left:269px;top:1167px">+61 400 555 218</p>
  <span class="abs foot-icon" style="left:332px"><svg width="9" height="9"><rect x="0.5" y="2" width="8" height="5.5" fill="var(--blue)"/><path d="M0.5 2L4.5 5L8.5 2" stroke="#fff" stroke-width=".8" fill="none"/></svg></span>
  <p class="abs foot-text" style="left:353px;top:1166px;font-size:7px;font-weight:400">hello@bramblehounds.example</p>
  <p class="abs foot-text" style="left:520px;top:1167px;width:154px;text-align:right;font-weight:400">©Copyright 2014 bramblehounds. All Rights Reserved.</p>
</footer>

</body>
</html>
```